Music Studio and Store Business Card and Logo Design

We need a business card and logo design for an existing Music Studio (Piano and Voice) which will soon expand to offer retail sheet music for all instruments including voice. The expanding store will not sell or lease instruments. We are a well known Fine Arts Studio for instruction to children, college students, and adults with 42 enrolled students and a wait list. We want something with simple elegance, but not archaic. Even a sleek modern look is okay. We do not want something childish or too fun looking because we do serve ages 5 - 62. We would also like the logo workable/transferable to signage for our new location opening in March. We like classic burgundy, black, deep blues, but are open to other suggestions. We included our studio brochure so you can get to know us a little better and some images we thought were interesting with the use of clef signs for the & and using note heads for the bottom or top of the letter "H"

Target Market(s)

All ages

Industry/Entity Type

Business

Contact Information for Business Card

H&H Music StudioPlattsburgh, NYWanda J. Haby and Oren M. Castaldi, Owners

Requirements
Must have
• Phone Number: (555) 817-4062
• Website: www.rbtonalartsroom.example
Nice to have
• Email: lorna@rbtonalartsroom.example
Should not have
• Any instruments on the card other than piano. Instrument pix is not a necessity.

```html
<!DOCTYPE html>
<html lang="en">
<head>
<meta charset="UTF-8">
<title>R&amp;B Music Studio — Business Card</title>
<link rel="stylesheet" href="https://fonts.googleapis.com/css2?family=Questrial&family=Source+Sans+3:wght@400;600&display=swap">
<style>
  :root {
    --page-bg: #e9e6e3;
    --card-white: #ffffff;
    --card-black: #000000;
    --ink: #111111;
  }
  * { margin: 0; padding: 0; box-sizing: border-box; }
  html, body {
    width: 1200px;
    height: 900px;
    overflow: hidden;
    background: var(--page-bg);
  }
  .canvas {
    position: relative;
    width: 1200px;
    height: 900px;
  }
  .card {
    position: absolute;
    overflow: hidden;
  }
  .card-front {
    left: 238px;
    top: 60px;
    width: 555px;
    height: 345px;
    background: var(--card-white);
  }
  .card-back {
    left: 457px;
    top: 518px;
    width: 560px;
    height: 343px;
    background: var(--card-black);
  }
  .diagonal {
    position: absolute;
    inset: 0;
  }
  .owners {
    position: absolute;
    left: 38px;
    top: 38px;
    font-family: "Source Sans 3", sans-serif;
    color: var(--ink);
  }
  .owner-name {
    font-weight: 600;
    font-size: 19px;
    line-height: 25px;
  }
  .owner-role {
    font-size: 14px;
    line-height: 22px;
    margin-top: 3px;
  }
  .location {
    font-size: 14px;
    line-height: 20px;
    margin-top: 20px;
  }
  .contact-line {
    font-size: 13px;
    line-height: 19px;
  }
  .studio-name {
    position: absolute;
    right: 34px;
    top: 182px;
    text-align: center;
    font-family: "Questrial", sans-serif;
    color: var(--card-white);
  }
  .studio-initials {
    font-size: 46px;
    line-height: 56px;
    letter-spacing: 2px;
  }
  .studio-word {
    font-size: 34px;
    line-height: 44px;
    margin-top: 8px;
  }
  .back-initials {
    position: absolute;
    inset: 0;
    display: flex;
    align-items: center;
    justify-content: center;
    font-family: "Questrial", sans-serif;
    font-size: 150px;
    color: var(--card-white);
    letter-spacing: 6px;
  }
</style>
</head>
<body>
<main class="canvas">
  <section class="card card-front">
    <svg class="diagonal" width="555" height="345" viewBox="0 0 555 345" aria-hidden="true">
      <polygon points="0,345 0,337 545,0 555,0 555,2 4,345" fill="var(--card-black)"/>
      <polygon points="18,345 555,11 555,345" fill="var(--card-black)"/>
    </svg>
    <div class="owners">
      <p class="owner-name">Lorna P. Quist</p>
      <p class="owner-name">Oren M. Castaldi</p>
      <p class="owner-role">Owners</p>
      <p class="location">Millbrook Falls, NY</p>
      <p class="contact-line">(555) 817-4062</p>
      <p class="contact-line">www.rbtonalartsroom.example</p>
    </div>
    <div class="studio-name">
      <p class="studio-initials">R&amp;B</p>
      <p class="studio-word">Music Studio</p>
    </div>
  </section>

  <section class="card card-back">
    <p class="back-initials">R&amp;B</p>
  </section>
</main>
</body>
</html>
```